Business Card Design for Training Business

Clear Path Coaching is a new business that delivers training and other services with a focus on topics related to mental health and wellbeing, for example, Wellmind Response Course, Resilience etc. We have a strong focus on evidence-based psychology and neuroscience. I have a logo which I will upload with the brief, so please consider colours that work well with the logo.
Target Market(s)
Adults, workplaces (particularly government and not-for-profits)
Industry/Entity Type
Business
Contact Information for Business Card
Head Strong TrainingSamantha SellwoodDirector0438 770 850sam@headstrongtraining.com.auwww.headstrongtraining.com.au

```html
<!DOCTYPE html>
<html lang="en">
<head>
<meta charset="utf-8">
<title>Clear Path Coaching – Business Card</title>
<link rel="stylesheet" href="https://fonts.googleapis.com/css2?family=Open+Sans:wght@300;400;700&display=swap">
<style>
  :root {
    --page-bg: #e9e6e1;
    --card-black: #0b0b0c;
    --card-sheen: #2a2b2d;
    --teal: #22c3c8;
    --edge-silver: #d9dcdd;
    --text-white: #f4f6f6;
    --text-soft: #c9cdce;
    --divider: #bfc3c4;
  }
  * { margin: 0; padding: 0; box-sizing: border-box; }
  html, body {
    width: 1200px; height: 1022px; overflow: hidden;
    background: var(--page-bg);
    font-family: "Open Sans", Arial, sans-serif;
  }
  .card {
    position: absolute; left: 100px; top: 225px;
    width: 1000px; height: 572px;
    border-radius: 26px; overflow: hidden;
    background: radial-gradient(ellipse at 35% 40%, var(--card-sheen) 0%, var(--card-black) 60%);
    box-shadow: 0 18px 40px rgba(0,0,0,0.25);
  }
  .card-bands { position: absolute; inset: 0; width: 1000px; height: 572px; }
  .brand {
    position: absolute; left: 60px; top: 160px; width: 370px;
    display: flex; flex-direction: column; align-items: center;
  }
  .brand-mark {
    width: 130px; height: 130px; border-radius: 50%;
    border: 3px solid var(--teal);
  }
  .brand-name {
    margin-top: 24px;
    display: flex; flex-direction: column; align-items: center;
    font-weight: 300; color: var(--text-soft);
    text-transform: uppercase; white-space: nowrap; line-height: 1.15;
  }
  .brand-name-main { font-size: 40px; letter-spacing: 3px; }
  .brand-name-sub { font-size: 20px; letter-spacing: 9px; margin-right: -9px; }
  .divider {
    position: absolute; left: 470px; top: 150px;
    width: 2px; height: 290px; background: var(--divider);
  }
  .contact { position: absolute; left: 510px; top: 170px; }
  .contact-name {
    font-weight: 700; font-size: 44px; color: var(--text-white); line-height: 1.1;
  }
  .contact-role {
    font-weight: 400; font-size: 26px; color: var(--teal); margin-top: 4px;
  }
  .contact-list { list-style: none; margin-top: 22px; }
  .contact-list li {
    display: flex; align-items: center; gap: 14px;
    font-size: 22px; color: var(--text-white); line-height: 1.6;
  }
  .contact-icon { width: 20px; height: 20px; flex: none; }
</style>
</head>
<body>
  <section class="card">
    <svg class="card-bands" viewBox="0 0 1000 572" aria-hidden="true">
      <path d="M0 0 H1000 V105 Q500 -5 0 105 Z" fill="var(--teal)"/>
      <path d="M0 105 Q500 -5 1000 105" fill="none" stroke="var(--edge-silver)" stroke-width="5"/>
      <path d="M0 572 H1000 V467 Q500 577 0 467 Z" fill="var(--teal)"/>
      <path d="M0 467 Q500 577 1000 467" fill="none" stroke="var(--edge-silver)" stroke-width="5"/>
    </svg>

    <div class="brand">
      <div class="brand-mark"></div>
      <div class="brand-name">
        <span class="brand-name-main">Clear Path</span>
        <span class="brand-name-sub">Coaching</span>
      </div>
    </div>

    <div class="divider"></div>

    <div class="contact">
      <h1 class="contact-name">Rebecca Tanfield</h1>
      <p class="contact-role">Director</p>
      <ul class="contact-list">
        <li>
          <svg class="contact-icon" viewBox="0 0 20 20" aria-hidden="true">
            <path d="M5 2 L8 6 L6.5 8 Q8.5 12 12 13.5 L14 12 L18 15 L16 18 Q8 18 2 6 Z" fill="var(--text-white)"/>
          </svg>
          0491 362 517
        </li>
        <li>
          <svg class="contact-icon" viewBox="0 0 20 20" aria-hidden="true">
            <rect x="2" y="4" width="16" height="12" rx="1.5" fill="none" stroke="var(--text-white)" stroke-width="2"/>
            <path d="M3 5 L10 11 L17 5" fill="none" stroke="var(--text-white)" stroke-width="2"/>
          </svg>
          bec@clearpathcoaching.example.au
        </li>
        <li>
          <svg class="contact-icon" viewBox="0 0 20 20" aria-hidden="true">
            <circle cx="10" cy="10" r="8" fill="none" stroke="var(--text-white)" stroke-width="2"/>
            <ellipse cx="10" cy="10" rx="3.5" ry="8" fill="none" stroke="var(--text-white)" stroke-width="1.5"/>
            <path d="M2 10 H18" stroke="var(--text-white)" stroke-width="1.5"/>
          </svg>
          www.clearpathcoaching.example.au
        </li>
      </ul>
    </div>
  </section>
</body>
</html>
```